Brivolt Technologies business card design

We need a business card designed with our new logo. it would be great if the card could communicate it is a technology based company.

Target Market(s)

system integrators

Industry/Entity Type

technology, IOT

Contact Information for Business Card

Name, designation, Address, telephone number, email address

Requirements
Must have
• logo and company name
Nice to have
• something to do with technology

```html
<!DOCTYPE html>
<html lang="en">
<head>
<meta charset="utf-8">
<title>Brivolt Technologies – Business Card</title>
<link rel="stylesheet" href="https://fonts.googleapis.com/css2?family=Arimo:wght@400;700&display=swap">
<style>
  :root {
    --backdrop: #969696;
    --card-light: #ffffff;
    --card-dark: #383838;
    --ink: #2b2b2b;
    --accent: #f7941d;
  }
  * { margin: 0; padding: 0; box-sizing: border-box; }
  html, body { width: 1200px; height: 1059px; overflow: hidden; }
  body {
    background: var(--backdrop);
    font-family: "Arimo", Arial, sans-serif;
    position: relative;
  }
  .card {
    position: absolute;
    width: 690px;
    height: 392px;
    border-radius: 24px;
    overflow: hidden;
  }
  .card--front { left: 256px; top: 89px; background: var(--card-light); color: var(--ink); }
  .card--back { left: 254px; top: 569px; background: var(--card-dark); }

  .contact { position: absolute; left: 29px; top: 92px; }
  .contact__name {
    color: var(--accent);
    font-weight: 700;
    font-size: 25px;
    line-height: 1;
    letter-spacing: 0.2px;
  }
  .contact__role { font-size: 17px; margin-top: 8px; }
  .contact__address { font-size: 17px; line-height: 21px; margin-top: 15px; }
  .contact__lines { list-style: none; margin-top: 14px; }
  .contact__lines li {
    font-size: 17px;
    line-height: 27px;
    display: flex;
    align-items: center;
    gap: 5px;
  }
  .contact__lines svg { width: 13px; height: 13px; flex: none; }

  .brand {
    position: absolute;
    display: flex;
    align-items: center;
    color: var(--accent);
    font-weight: 700;
    text-transform: uppercase;
  }
  .brand__square { background: var(--accent); flex: none; }
  .brand--front { left: 420px; top: 178px; gap: 12px; font-size: 30px; letter-spacing: 1px; color: var(--ink); }
  .brand--front .brand__square { width: 30px; height: 30px; }
  .brand--back { left: 120px; top: 152px; gap: 22px; }
  .brand--back .brand__square { width: 84px; height: 84px; }
  .brand__words { display: flex; flex-direction: column; line-height: 1; }
  .brand__main { font-size: 58px; letter-spacing: 1px; }
  .brand__sub { font-size: 24px; letter-spacing: 12px; margin-top: 10px; }
</style>
</head>
<body>

<section class="card card--front">
  <div class="contact">
    <h1 class="contact__name">DANIEL MARSH</h1>
    <p class="contact__role">CEO/Founder</p>
    <p class="contact__address">5741 Street Name<br>Country Name AB 8754</p>
    <ul class="contact__lines">
      <li>
        <svg viewBox="0 0 16 16" aria-hidden="true"><path fill="#f7941d" d="M3.6 1.2l2.3 2.6-1.3 1.6c.8 2 2.3 3.5 4.1 4.3l1.6-1.3 2.6 2.3-1.5 2.4C6.2 13.5 2 9.3 1.2 3.3z"/></svg>
        (123) 555-0148
      </li>
      <li>
        <svg viewBox="0 0 16 16" aria-hidden="true"><rect x="1" y="3" width="14" height="10" rx="1" fill="#f7941d"/><path d="M1.5 4l6.5 5 6.5-5" stroke="#fff" stroke-width="1.3" fill="none"/></svg>
        info@brivolttechnologies.com
      </li>
      <li>
        <svg viewBox="0 0 16 16" aria-hidden="true"><g fill="none" stroke="#f7941d" stroke-width="1.3"><circle cx="8" cy="8" r="6.5"/><ellipse cx="8" cy="8" rx="3" ry="6.5"/><path d="M1.5 8h13M2.5 4.8h11M2.5 11.2h11"/></g></svg>
        www.brivolttechnologies.com
      </li>
    </ul>
  </div>
  <div class="brand brand--front">
    <span class="brand__square"></span>
    <span>Brivolt</span>
  </div>
</section>

<section class="card card--back">
  <div class="brand brand--back">
    <span class="brand__square"></span>
    <span class="brand__words">
      <span class="brand__main">Brivolt</span>
      <span class="brand__sub">Technologies</span>
    </span>
  </div>
</section>

</body>
</html>
```